Packaging design for a reclosable bag for our product

We have a logo, and we need to put it on packaging for our product and while we want the look to be simple, we want it to follow good design principles and also contain spaces for other product descriptions.

There will be 5 sizes at launch so I'd like 5 variations, one for each size.

I've included a few mockups of the type of bag that I made but they are all just rough ideas that I had.

I want the brand to look scientific and methodical and even a bit quirky, as in "wow this is a serious product but also a bit unusual."

```html
<!DOCTYPE html>
<html lang="en">
<head>
<meta charset="utf-8">
<title>KV3 Bias Lighting – Pouch Range</title>
<link rel="stylesheet" href="https://fonts.googleapis.com/css2?family=Montserrat:wght@300;400;800&display=swap">
<style>
  :root {
    --bg: #ffffff;
    --pouch: #1c1c1d;
    --pouch-seal: #262627;
    --seal-line: #101010;
    --ink-light: #f2f2f2;
    --ink-dark: #111111;
    --size-xl: #1196de;
    --size-l: #e3171f;
  }
  * { margin: 0; padding: 0; box-sizing: border-box; }
  html, body {
    width: 1200px; height: 1200px; overflow: hidden;
    background: var(--bg);
    font-family: "Montserrat", Arial, sans-serif;
  }
  .range { position: relative; width: 1200px; height: 1200px; }

  .pouch {
    position: absolute;
    background: var(--pouch);
    border-radius: 20px 20px 0 0;
    overflow: hidden;
  }
  .pouch--xl { left: 194px; top: 242px; width: 492px; height: 730px; --accent: var(--size-xl); }
  .pouch--l  { left: 598px; top: 344px; width: 438px; height: 640px; --accent: var(--size-l); }

  .pouch__seal {
    position: absolute; left: 0; right: 0; top: 64px; height: 22px;
    background: var(--pouch-seal);
    border-top: 2px solid var(--seal-line);
    border-bottom: 3px solid var(--seal-line);
  }
  .pouch__stripe {
    position: absolute; left: 0; top: 0; bottom: 0; width: 64px;
    background: var(--accent);
  }
  .pouch__stripe .pouch__seal { background: rgba(0,0,0,0.08); border-color: rgba(0,0,0,0.18); }

  .size-tag {
    position: absolute; left: 10px;
    writing-mode: vertical-rl; transform: rotate(180deg);
    display: flex; align-items: center;
    color: var(--ink-dark); line-height: 1;
  }
  .pouch--xl .size-tag { bottom: 130px; }
  .pouch--l  .size-tag { bottom: 148px; left: 8px; }
  .size-tag__code { font-weight: 800; font-size: 44px; }
  .size-tag__rule { width: 64px; height: 4px; background: var(--ink-dark); margin: 10px 0; writing-mode: horizontal-tb; transform: translateX(-10px); }
  .size-tag__length { font-weight: 800; font-size: 40px; }
  .size-tag__unit { font-weight: 400; font-size: 32px; margin-top: 4px; }
  .pouch--l .size-tag__code { font-size: 38px; }
  .pouch--l .size-tag__length { font-size: 36px; }
  .pouch--l .size-tag__unit { font-size: 28px; }

  .label { position: absolute; color: var(--ink-light); }
  .pouch--xl .label { left: 98px; top: 270px; }
  .pouch--l  .label { left: 92px; top: 226px; }

  .label__brand { font-weight: 800; font-size: 46px; letter-spacing: -1px; line-height: 1; }
  .label__product { font-weight: 400; font-size: 32px; margin-top: 22px; line-height: 1.1; }
  .label__size { font-weight: 400; font-size: 19px; margin-top: 2px; }
  .label__spec { margin-top: 62px; font-weight: 400; line-height: 1.3; }
  .label__spec-main { font-size: 22px; }
  .label__spec-sub { font-size: 19px; }

  .pouch--l .label__brand { font-size: 42px; }
  .pouch--l .label__product { font-size: 29px; margin-top: 22px; }
  .pouch--l .label__size { font-size: 18px; }
  .pouch--l .label__spec { margin-top: 52px; }
  .pouch--l .label__spec-main { font-size: 20px; }
  .pouch--l .label__spec-sub { font-size: 18px; }
</style>
</head>
<body>
<main class="range">

  <section class="pouch pouch--xl" aria-label="Extra large pouch, 5 meters">
    <div class="pouch__seal"></div>
    <div class="pouch__stripe">
      <div class="pouch__seal"></div>
      <div class="size-tag">
        <span class="size-tag__code">XL</span>
        <span class="size-tag__rule"></span>
        <span class="size-tag__length">5</span>
        <span class="size-tag__unit">meters</span>
      </div>
    </div>
    <div class="label">
      <div class="label__brand">KV3</div>
      <div class="label__product">Bias Lighting</div>
      <div class="label__size">Extra large</div>
      <div class="label__spec">
        <div class="label__spec-main">Simulated D65 CRI 90+</div>
        <div class="label__spec-sub">6500K White Bias Lighting</div>
      </div>
    </div>
  </section>

  <section class="pouch pouch--l" aria-label="Large pouch, 4 meters">
    <div class="pouch__seal"></div>
    <div class="pouch__stripe">
      <div class="pouch__seal"></div>
      <div class="size-tag">
        <span class="size-tag__code">L</span>
        <span class="size-tag__rule"></span>
        <span class="size-tag__length">4</span>
        <span class="size-tag__unit">meters</span>
      </div>
    </div>
    <div class="label">
      <div class="label__brand">KV3</div>
      <div class="label__product">Bias Lighting</div>
      <div class="label__size">Extra large</div>
      <div class="label__spec">
        <div class="label__spec-main">Simulated D65 CRI 90+</div>
        <div class="label__spec-sub">6500K White Bias Lighting</div>
      </div>
    </div>
  </section>

</main>
</body>
</html>
```